Goat's Milk Soap

International product development company seeking designs for the following soap label:

Hand crafted in Mt Carrowby QLD Australia, Fernleigh Valley
Second Generation Goat Farmers
Soap is hand made in appearance but gives an instant soothing feel when used
High in Vegetable oils and pure fresh goats milk (no powders used)
Give the emotional feel of Quality and Hand crafted
Label must stimulate an emotional response visually
Label must deliver to the customer anticipation for use.
Would anticipate that the label will be produced on a matte finish brown paper label or similar.

Logo should be no larger than 50mm x 50mm
Label should measure around 120mm x 70mm

It Company

```html
<!DOCTYPE html>
<html lang="en">
<head>
<meta charset="utf-8">
<title>Goat's Milk Soap — Label</title>
<link rel="stylesheet" href="https://fonts.googleapis.com/css2?family=Josefin+Sans:wght@600&family=Oswald:wght@300&family=Roboto+Slab:wght@800&display=swap">
<style>
  :root {
    --kraft-light: #c4b38e;
    --kraft-mid: #ab9c78;
    --kraft-dark: #8f8767;
    --ink: #141210;
    --art-tone: #5f5a4c;
    --sprig-tone: #3a362d;
  }
  html, body {
    margin: 0;
    padding: 0;
    overflow: hidden;
    background: var(--kraft-mid);
  }
  .label {
    position: relative;
    width: 1200px;
    height: 725px;
    overflow: hidden;
    background:
      radial-gradient(ellipse 70% 80% at 70% 35%, var(--kraft-light) 0%, transparent 70%),
      radial-gradient(ellipse 60% 70% at 5% 70%, var(--kraft-dark) 0%, transparent 75%),
      linear-gradient(160deg, var(--kraft-mid) 0%, var(--kraft-light) 55%, var(--kraft-mid) 100%);
  }
  .emblem {
    position: absolute;
    left: 0;
    top: 0;
    width: 1200px;
    height: 725px;
  }
  .emblem-frame {
    fill: none;
    stroke: var(--ink);
    stroke-width: 5;
    stroke-linejoin: round;
  }
  .product-name {
    position: absolute;
    left: 0;
    width: 1200px;
    text-align: center;
    color: var(--ink);
    margin: 0;
  }
  .product-name--top {
    top: 212px;
    font-family: "Oswald", sans-serif;
    font-weight: 300;
    font-size: 54px;
    letter-spacing: 3px;
    line-height: 1;
  }
  .product-name--bottom {
    top: 430px;
    left: 6px;
    font-family: "Roboto Slab", serif;
    font-weight: 800;
    font-size: 50px;
    letter-spacing: 2px;
    line-height: 1;
  }
  .tagline {
    position: absolute;
    left: 0;
    width: 1200px;
    margin: 0;
    text-align: center;
    font-family: "Josefin Sans", sans-serif;
    font-weight: 600;
    font-size: 16px;
    letter-spacing: 4.6px;
    color: var(--ink);
    text-transform: uppercase;
    line-height: 1;
  }
  .tagline--ingredients { top: 591px; }
  .tagline--origin { top: 628px; }
</style>
</head>
<body>
  <main class="label">
    <svg class="emblem" viewBox="0 0 1200 725" xmlns="http://www.w3.org/2000/svg">
      <path class="emblem-frame"
        d="M600,130 C612,150 630,168 655,180 L790,196 C792,214 806,228 818,232 L818,468 C806,472 792,486 790,502 L655,518 C630,530 612,545 600,560 C588,545 570,530 545,518 L410,502 C408,486 394,472 386,468 L386,232 C394,228 408,214 410,196 L545,180 C570,168 588,150 600,130 Z"/>
      <rect class="emblem-goat" x="502" y="272" width="202" height="160" rx="10"
        fill="var(--art-tone)" opacity="0.55" role="img"
        aria-label="Engraved-style illustration of a goat standing on grass"/>
      <rect class="emblem-sprig emblem-sprig--left" x="450" y="404" width="44" height="74" rx="18"
        fill="var(--sprig-tone)" opacity="0.45" role="img" aria-label="Small leafy sprig ornament"/>
      <rect class="emblem-sprig emblem-sprig--right" x="708" y="404" width="44" height="74" rx="18"
        fill="var(--sprig-tone)" opacity="0.45" role="img" aria-label="Small leafy sprig ornament"/>
    </svg>

    <h1 class="product-name product-name--top">GOAT’S MILK</h1>
    <p class="product-name product-name--bottom">SOAP</p>

    <p class="tagline tagline--ingredients">Quality soap high in vegetable oils and pure fresh goat’s milk</p>
    <p class="tagline tagline--origin">Handcrafted in Mt Carrowby QLD Australia, Fernleigh Valley</p>
  </main>
</body>
</html>
```